Corvin Ridge Software PowerPoint template

We are a software company selling endpoint visibility, access and security technology to enterprise-level IT departments.
Our technology helps organizations gain comprehensive visibility into and control over devices accessing their corporate network so they can quickly identify and address suspicious activity on the network that could lead to potential threats like data breaches.
This technology can cost organizations upwards of $1M - depending on the size of the organization. Our primary clients are Vestral 2,000 companies.
We want a professional, polished PowerPoint template that we can use for all company presentations. Please include:
Title page
Section page
General info page
Thank you page
Logo options and color specs are attached.
Please include our tagline on at least the title page: Discover the edge. Optimize the whole.
Reason: Seeking more options. Looking for a clean design that uses lots of white space.
Software

```html
<!DOCTYPE html>
<html lang="en">
<head>
<meta charset="utf-8">
<title>Corvin Ridge Software – Agenda</title>
<link href="https://fonts.googleapis.com/css2?family=Exo+2:wght@600;700&family=Hind:wght@400;500;600&display=swap" rel="stylesheet">
<style>
  :root {
    --accent: #d07a56;
    --accent-soft: #e6bfae;
    --brand-red: #9b2a2a;
    --ink: #1a1a1a;
    --muted: #555555;
    --rule: #bdbdbd;
    --paper: #ffffff;
  }
  html, body {
    margin: 0;
    padding: 0;
    overflow: hidden;
    background: var(--paper);
  }
  .slide {
    position: relative;
    width: 1200px;
    height: 849px;
    overflow: hidden;
    background: var(--paper);
    font-family: "Hind", Arial, sans-serif;
    color: var(--ink);
  }
  .rule {
    position: absolute;
    left: 0;
    width: 869px;
    height: 1px;
    background: var(--rule);
  }
  .rule--top { top: 58px; }
  .rule--bottom { top: 767px; }

  .header-meta {
    position: absolute;
    right: 50px;
    top: 44px;
    text-align: right;
  }
  .header-meta__title {
    font-size: 20px;
    line-height: 26px;
    color: var(--brand-red);
    font-weight: 500;
    letter-spacing: 0.2px;
  }
  .header-meta__date {
    font-size: 18px;
    line-height: 24px;
    font-weight: 600;
    color: var(--ink);
  }
  .header-bar {
    position: absolute;
    left: 1163px;
    top: 46px;
    width: 6px;
    height: 51px;
    background: var(--accent);
  }

  .side-texture {
    position: absolute;
    left: 0;
    top: 142px;
    width: 264px;
    height: 542px;
    background: radial-gradient(ellipse at 30% 50%, var(--accent-soft) 0%, rgba(230,191,174,0.35) 40%, rgba(255,255,255,0) 75%);
  }

  .agenda-title {
    position: absolute;
    left: 280px;
    top: 118px;
    margin: 0;
    font-family: "Exo 2", Arial, sans-serif;
    font-weight: 700;
    font-size: 68px;
    line-height: 90px;
    color: var(--accent);
  }

  .agenda-list {
    position: absolute;
    left: 292px;
    top: 249px;
    width: 720px;
    margin: 0;
    padding: 0;
    list-style: none;
  }
  .agenda-list__item {
    position: relative;
    padding-left: 31px;
    margin-bottom: 34px;
    font-size: 20.5px;
    line-height: 26px;
  }
  .agenda-list__item::before {
    content: "";
    position: absolute;
    left: 0;
    top: 7px;
    width: 14px;
    height: 14px;
    border-radius: 50%;
    background: var(--accent);
  }

  .page-number {
    position: absolute;
    left: 1114px;
    top: 388px;
    width: 54px;
    height: 54px;
    border-radius: 50%;
    background: var(--accent);
    color: var(--paper);
    font-size: 17px;
    line-height: 56px;
    text-align: center;
  }

  .footer-copy {
    position: absolute;
    left: 88px;
    top: 777px;
    font-size: 12px;
    color: var(--muted);
  }

  .brand {
    position: absolute;
    left: 880px;
    top: 744px;
    display: flex;
    align-items: center;
    gap: 14px;
  }
  .brand__mark {
    width: 40px;
    height: 40px;
    border-radius: 50%;
    background: var(--accent);
  }
  .brand__name {
    font-size: 22px;
    line-height: 24px;
    font-weight: 600;
    letter-spacing: 2px;
    color: var(--brand-red);
    text-transform: uppercase;
  }
</style>
</head>
<body>
<div class="slide">
  <div class="rule rule--top"></div>
  <div class="header-meta">
    <div class="header-meta__title">PPT HEADING GOES HERE</div>
    <div class="header-meta__date">FEB, 2015</div>
  </div>
  <div class="header-bar"></div>

  <div class="side-texture" role="img" aria-label="Soft field of faint peach and grey circles as side decoration"></div>

  <h1 class="agenda-title">Agenda</h1>

  <ul class="agenda-list">
    <li class="agenda-list__item">US Corporation with 16 years Lease and Loan Management Software experience US Corporation with 16 years Lease and Loan Management Software experience</li>
    <li class="agenda-list__item">US Corporation with 16 years Lease and Loan Management Software experience US Corporation with 16 years Lease and L</li>
    <li class="agenda-list__item">US Corporation with 16 years Lease and</li>
    <li class="agenda-list__item">US Corporation with 16 years Lease and Loan Management Software experience US Corporation with 16 y</li>
    <li class="agenda-list__item">US Corporation with 16 years Lease and</li>
  </ul>

  <div class="page-number">01</div>

  <div class="rule rule--bottom"></div>
  <div class="footer-copy">©2015 Corvin Ridge Software</div>

  <div class="brand">
    <div class="brand__mark"></div>
    <div class="brand__name">Corvin Ridge<br>Software</div>
  </div>
</div>
</body>
</html>
```